BrivoTerna. Lantern of the Steady Harvest. Business card

Professional business card for BrivoTerna (Lantern of the Steady Harvest)
My rationale: Strategy-> Execution-> Results-> Value that lead to the BrivoTerna name: We put the Lantern of the Steady Harvest.
We deliver value to our customers helping them at defining a good strategy (cyan arrow). 90% of well formulated strategies fail due to poor execution so we also consider strategical execution very important (green arrow). Due to the execution we obtain the results (blue arrow). Finally, the results provide feedback to redefine strategy, and the new strategy has to be executed and new results obtained providing new feedback and on and on. It's like a wheel that finally, must create corporate value: value for shareholders, staholders, employees, providers...-

Target Market(s)

CEOs and steering comitees , invewrnent funds

Industry/Entity Type

Business Consultant

Contact Information for Business Card

Teodoro Vinsquel
CEO & Founder
teodoro.vinsquel@brivoterna-example.com
Mobile: +34 655.803.912
www.brivoterna-example.com

Colors

Designer to choose colors to be used in the design.

Requirements
Nice to have
• Nice to hace the words: Strategy, execution, results
• Nice to vave the claim: Lantern of the Steady Harvest
• The three colors should be shown:
• cyan for STRATEGY
• green for EXECUTION
• blue for RESULTS
Should not have
• Complete black background

```html
<!DOCTYPE html>
<html lang="en">
<head>
<meta charset="utf-8">
<title>BrivoTerna — Business Card</title>
<link rel="stylesheet" href="https://fonts.googleapis.com/css2?family=Questrial&display=swap">
<style>
  :root {
    --stage: #2e2e2e;
    --paper: #ffffff;
    --navy: #0a3596;
    --green: #8cc63f;
    --cyan: #00aeef;
    --grey-text: #5a5a5a;
    --ink: #2b2b2b;
  }
  * { box-sizing: border-box; margin: 0; padding: 0; }
  html, body {
    width: 1200px; height: 866px; overflow: hidden;
    background: var(--stage);
    font-family: "Questrial", "Century Gothic", sans-serif;
  }
  .stage {
    width: 1200px; height: 866px;
    display: flex; align-items: center; justify-content: center; gap: 40px;
  }
  .card {
    position: relative;
    width: 560px; height: 350px;
    overflow: hidden;
    box-shadow: 0 10px 24px rgba(0,0,0,.45);
  }

  /* Front */
  .card-front { background: var(--paper); }
  .holder { position: absolute; left: 40px; top: 38px; }
  .holder-name { color: var(--navy); font-size: 24px; letter-spacing: .3px; }
  .holder-role { color: var(--grey-text); font-size: 14px; margin-top: 2px; }

  .contact { position: absolute; left: 40px; top: 178px; list-style: none; }
  .contact li {
    display: flex; align-items: center; gap: 8px;
    color: var(--ink); font-size: 13px; line-height: 20px;
  }
  .contact svg { width: 13px; height: 13px; flex: none; }

  .brand {
    position: absolute; right: 40px; top: 150px;
    display: flex; align-items: center; gap: 12px;
  }
  .brand-dot { width: 18px; height: 18px; border-radius: 50%; background: var(--navy); }
  .brand-name { color: var(--navy); font-size: 44px; letter-spacing: -.5px; }

  .pillars {
    position: absolute; right: 40px; top: 232px;
    list-style: none; text-align: right; font-size: 17px; line-height: 19px;
  }
  .pillar-strategy { color: var(--navy); }
  .pillar-execution { color: var(--green); }
  .pillar-results { color: var(--cyan); }

  .tri-band {
    position: absolute; left: 0; right: 0; bottom: 0; height: 10px;
    display: flex;
  }
  .tri-band span { flex: 1; }
  .tri-band .band-blue { background: var(--navy); }
  .tri-band .band-green { background: var(--green); }
  .tri-band .band-cyan { background: var(--cyan); }

  /* Back */
  .card-back {
    background: linear-gradient(35deg, var(--navy) 0%, #1d5fb0 18%, var(--green) 48%, #5fcf7a 66%, var(--cyan) 100%);
    color: var(--paper);
  }
  .back-lockup {
    position: absolute; left: 0; right: 0; top: 50%;
    transform: translateY(-50%);
    text-align: center;
  }
  .back-name { font-size: 58px; letter-spacing: -.5px; }
  .back-claim { font-size: 13px; letter-spacing: 1.2px; text-transform: uppercase; margin-top: 4px; }
</style>
</head>
<body>
<main class="stage">

  <section class="card card-front" aria-label="Business card front">
    <div class="holder">
      <p class="holder-name">Teodoro Vinsquel</p>
      <p class="holder-role">CEO &amp; Founder</p>
    </div>

    <ul class="contact">
      <li>
        <svg viewBox="0 0 16 16" aria-hidden="true"><path fill="#2b2b2b" d="M2 5c0-1.5 2-3 6-3s6 1.5 6 3v1h-3V5H5v1H2zM4 7h8l2 7H2z"/></svg>
        +34 655.803.912
      </li>
      <li>
        <svg viewBox="0 0 16 16" aria-hidden="true"><rect x="1" y="3" width="14" height="10" fill="#2b2b2b"/><path d="M1.5 3.5 8 9l6.5-5.5" stroke="#fff" stroke-width="1.3" fill="none"/></svg>
        teodoro.vinsquel@brivoterna-example.com
      </li>
      <li>
        <svg viewBox="0 0 16 16" aria-hidden="true"><circle cx="8" cy="8" r="7" fill="#2b2b2b"/><ellipse cx="8" cy="8" rx="3" ry="7" stroke="#fff" fill="none"/><path d="M1 8h14" stroke="#fff"/></svg>
        www.brivoterna-example.com
      </li>
    </ul>

    <div class="brand">
      <span class="brand-dot" aria-hidden="true"></span>
      <span class="brand-name">BrivoTerna</span>
    </div>

    <ul class="pillars">
      <li class="pillar-strategy">Strategy</li>
      <li class="pillar-execution">Execution</li>
      <li class="pillar-results">Results</li>
    </ul>

    <div class="tri-band" aria-hidden="true">
      <span class="band-blue"></span><span class="band-green"></span><span class="band-cyan"></span>
    </div>
  </section>

  <section class="card card-back" aria-label="Business card back">
    <div class="back-lockup">
      <p class="back-name">BrivoTerna</p>
      <p class="back-claim">Lantern of the Steady Harvest</p>
    </div>
  </section>

</main>
</body>
</html>
```